Harborview Estates Business Card for Apartment Buildings

Create business cards for resident managers who run apartment buildings. The audience is the public who are searching for apartment rentals, and current residents who live at the apartment building. Key design element will be incorporating the company logo, however, the logo cannot dominate. The building name and manager name are more important than the logo. Current business card design leaves little room for copy, so we may need to reduce the size on the current card to allow for more space for copy.

Target Market(s)

Adults 18-65 years of age, who are looking for an apartment rental, plus current residents who live at our apartment buildings.

Industry/Entity Type

Property Management

Contact Information for Business Card

A major design element will be use of the company logo. Important property and manager contact information must be part of the design. The size of the logo will need to be reduced to make room for building and manager contact copy.

Font styles to use
Sans Serif

Colors
3176b5
000000
959595
ffffff

Requirements
Must have
• 1) Incorporate the company logo.
• 2) Use the company colors (dark blue, black/grey, over white).
• 3) FEATURE THE BUILDING NAME
• 4) FEATURE THE MANAGER NAME
• 5) The company name is less important than BUILDING and MANAGER
• 6) Manager contact information
• **SEE ATTACHED CREATIVE BRIEF**
Nice to have
• 1) Back of card logo watermark
• 2) Ability to write notes on back of carfd
Should not have
• Avoid letting the company logo dominate the card, the building name and manager are more important than the company logo.

```html
<!DOCTYPE html>
<html lang="en">
<head>
<meta charset="utf-8">
<title>Harborview Estates Business Card</title>
<link rel="stylesheet" href="https://fonts.googleapis.com/css2?family=Roboto:wght@400;500;700&family=Roboto+Condensed:wght@700&display=swap">
<style>
  :root {
    --brand-blue: #1e8fdc;
    --card-black: #1d1d1f;
    --backdrop: #3b3b3d;
    --text-white: #ffffff;
    --text-grey: #959595;
  }
  * { margin: 0; padding: 0; box-sizing: border-box; }
  html, body { width: 799px; height: 1200px; overflow: hidden; }
  body {
    background: var(--backdrop);
    font-family: "Roboto", Arial, sans-serif;
    display: flex;
    flex-direction: column;
    align-items: center;
    justify-content: space-around;
    padding: 80px 0;
  }
  .card {
    width: 660px;
    height: 378px;
    background: var(--card-black);
    border-radius: 4px;
    box-shadow: 0 10px 26px rgba(0,0,0,0.45);
    position: relative;
  }
  /* Front */
  .card-front {
    display: flex;
    align-items: center;
    justify-content: center;
  }
  .company-name {
    font-family: "Roboto", Arial, sans-serif;
    font-weight: 700;
    font-size: 28px;
    letter-spacing: 1px;
    color: var(--brand-blue);
    text-transform: uppercase;
    display: flex;
    align-items: center;
    gap: 14px;
    white-space: nowrap;
  }
  .company-mark {
    width: 34px;
    height: 34px;
    background: var(--brand-blue);
    flex-shrink: 0;
  }
  /* Back */
  .card-back {
    display: flex;
    align-items: center;
    justify-content: space-between;
    padding: 0 40px;
  }
  .manager {
    display: flex;
    align-items: center;
    gap: 12px;
  }
  .manager-mark {
    width: 40px;
    height: 40px;
    background: var(--brand-blue);
    flex-shrink: 0;
  }
  .manager-name {
    font-family: "Roboto Condensed", "Arial Narrow", sans-serif;
    font-weight: 700;
    font-size: 34px;
    line-height: 1;
    color: var(--brand-blue);
    text-transform: uppercase;
    white-space: nowrap;
  }
  .manager-title {
    font-weight: 700;
    font-size: 13px;
    letter-spacing: 2.5px;
    color: var(--text-white);
    text-transform: uppercase;
    margin-top: 4px;
    white-space: nowrap;
  }
  .contact-list {
    list-style: none;
    color: var(--text-white);
    font-size: 15px;
    line-height: 1.45;
  }
  .contact-list li {
    display: flex;
    align-items: center;
    gap: 8px;
    white-space: nowrap;
  }
  .contact-list svg {
    width: 13px;
    height: 13px;
    fill: none;
    stroke: var(--brand-blue);
    stroke-width: 2;
    flex-shrink: 0;
  }
  .contact-list .address { display: block; }
</style>
</head>
<body>
  <section class="card card-front">
    <div class="company-name"><span class="company-mark"></span>Harborview Estates LLC</div>
  </section>

  <section class="card card-back">
    <div class="manager">
      <span class="manager-mark"></span>
      <div>
        <div class="manager-name">Dana Whitfield</div>
        <div class="manager-title">Property Manager</div>
      </div>
    </div>
    <ul class="contact-list">
      <li><svg viewBox="0 0 24 24"><path d="M5 3h4l2 5-3 2a12 12 0 0 0 6 6l2-3 5 2v4a2 2 0 0 1-2 2A18 18 0 0 1 3 5a2 2 0 0 1 2-2z"/></svg>555-014-2231</li>
      <li><svg viewBox="0 0 24 24"><rect x="6" y="3" width="12" height="6"/><rect x="3" y="9" width="18" height="8"/><rect x="7" y="14" width="10" height="7"/></svg>555-014-7780</li>
      <li><svg viewBox="0 0 24 24"><rect x="3" y="5" width="18" height="14"/><path d="M3 5l9 8 9-8"/></svg>dana@harborviewestates.us</li>
      <li><svg viewBox="0 0 24 24"><circle cx="12" cy="12" r="9"/><path d="M3 12h18M12 3c4 4 4 14 0 18M12 3c-4 4-4 14 0 18"/></svg>www.harborviewestates.us</li>
      <li class="address">1207 Lantern Bay Drive<br>#B210 Seaside, CA 90000</li>
    </ul>
  </section>
</body>
</html>
```